Simple Logo Design for Semi-Clear Plastic Frosted Card stock

Create a business card on frosted plastic. compliment existing logo elements with a tree trunk, roots, or seed at the lower half and the full logo both on the front.

Contact information will go on a solid portion of the back of this design since this card stock is semi-transparent.

It is important to consider this plastic card stock medium in your design. I found helpful tips and guides listed at vellaprint-sample.net: be careful to understand ink printed on plastic cards cannot have too much of a consistent print area or risks peeling and fine lines can easily scratch off.
Updates

2" x 3.5" 20PT Clear Plastic Business cards with Round corners Please get info or templates here: https://www.vellaprint-sample.net/product-detail/2-x-35-20pt-clear-plastic-business-cards-with-round-corners

Target Market(s)

Not for profit- religion

Industry/Entity Type

Business

Must include complementary elements to the existing logo

Font styles to use
Decorative

Colors
000000

Requirements
Must have
• Elements of community, nature and oneness. Such as: seed, roots, tree trunk, etc.
• Three lines of space on the back for Name, Title, Phone Number.
Nice to have
• I like a light use of decorative elements
Should not have
• No eyes, from faces or animals.

```html
<!DOCTYPE html>
<html lang="en">
<head>
<meta charset="utf-8">
<title>Steadfast Grove — Business Card</title>
<link rel="stylesheet" href="https://fonts.googleapis.com/css2?family=Questrial&family=Open+Sans:wght@400&display=swap">
<style>
  :root {
    --page-bg: #ecebe8;
    --frost-top: #f4f1f0;
    --frost-bottom: #e6dedd;
    --paper: #f7f7f5;
    --teal: #236b67;
    --teal-text: #236b66;
    --leaf-green: #3f9a3c;
    --white: #ffffff;
  }
  * { margin: 0; padding: 0; box-sizing: border-box; }
  html, body {
    width: 1200px;
    height: 900px;
    overflow: hidden;
    background: var(--page-bg);
  }
  .canvas {
    position: relative;
    width: 1200px;
    height: 900px;
  }
  .card {
    position: absolute;
    border-radius: 10px;
    overflow: hidden;
    box-shadow: 0 4px 14px rgba(0, 0, 0, 0.12);
  }
  .card--front {
    left: 65px;
    top: 42px;
    width: 607px;
    height: 374px;
    background: linear-gradient(180deg, var(--frost-top), var(--frost-bottom));
  }
  .card--back {
    left: 388px;
    top: 505px;
    width: 567px;
    height: 352px;
    background: var(--paper);
  }
  .card__band {
    position: absolute;
    inset: 0;
    width: 100%;
    height: 100%;
  }
  .brand {
    position: absolute;
    left: 0;
    right: 0;
    text-align: center;
    font-family: "Questrial", "Century Gothic", sans-serif;
  }
  .brand__mark {
    display: block;
    margin: 0 auto;
    border-radius: 50%;
    background: var(--teal);
  }
  .brand__name {
    display: block;
    color: var(--teal-text);
    letter-spacing: 0.5px;
    line-height: 1;
    white-space: nowrap;
  }
  .brand__tagline {
    display: block;
    color: var(--teal-text);
    letter-spacing: 1px;
    text-transform: uppercase;
    white-space: nowrap;
  }
  .card--front .brand { top: 54px; }
  .card--front .brand__mark { width: 86px; height: 86px; margin-bottom: 14px; }
  .card--front .brand__name { font-size: 33px; }
  .card--front .brand__tagline { font-size: 12px; margin-top: 4px; }

  .card--back .brand { top: 98px; }
  .card--back .brand__mark { width: 96px; height: 96px; margin-bottom: 14px; }
  .card--back .brand__name { font-size: 33px; }
  .card--back .brand__tagline { font-size: 12px; margin-top: 4px; }

  .contact {
    position: absolute;
    top: 282px;
    left: 0;
    width: 100%;
    font-family: "Open Sans", Arial, sans-serif;
    color: var(--white);
  }
  .contact__person {
    position: absolute;
    right: 311px;
    text-align: right;
  }
  .contact__name { font-size: 23px; line-height: 1.2; }
  .contact__title { font-size: 15px; line-height: 1.3; }
  .contact__phone {
    position: absolute;
    left: 334px;
    top: 17px;
    font-size: 15px;
    display: flex;
    align-items: center;
    gap: 6px;
  }
  .contact__phone svg { width: 12px; height: 12px; }
</style>
</head>
<body>
<main class="canvas">

  <section class="card card--front" aria-label="Card front">
    <svg class="card__band" viewBox="0 0 607 374" preserveAspectRatio="none" aria-hidden="true">
      <path d="M0,278 Q300,226 607,270 L607,374 L0,374 Z" fill="var(--teal)"/>
      <path d="M150,238 Q420,205 607,258 L607,266 Q420,222 150,238 Z" fill="var(--leaf-green)"/>
    </svg>
    <div class="brand">
      <span class="brand__mark"></span>
      <span class="brand__name">STEADFAST GROVE</span>
      <span class="brand__tagline">Wisdom, Fellowship &amp; Harmony</span>
    </div>
    <div class="contact">
      <div class="contact__person">
        <div class="contact__name">Daniel Reyes</div>
        <div class="contact__title">Managing Director</div>
      </div>
      <div class="contact__phone">
        <svg viewBox="0 0 24 24" aria-hidden="true">
          <path fill="var(--white)" d="M6.6 10.8c1.4 2.8 3.8 5.1 6.6 6.6l2.2-2.2c.3-.3.7-.4 1-.2 1.1.4 2.3.6 3.6.6.6 0 1 .4 1 1V20c0 .6-.4 1-1 1C10.6 21 3 13.4 3 4c0-.6.4-1 1-1h3.5c.6 0 1 .4 1 1 0 1.3.2 2.5.6 3.6.1.3 0 .7-.2 1L6.6 10.8z"/>
        </svg>
        <span>(055)-312-4086</span>
      </div>
    </div>
  </section>

  <section class="card card--back" aria-label="Card back">
    <div class="brand">
      <span class="brand__mark"></span>
      <span class="brand__name">STEADFAST GROVE</span>
      <span class="brand__tagline">Wisdom, Fellowship &amp; Harmony</span>
    </div>
  </section>

</main>
</body>
</html>
```